New Business Card Design Project

Use the flyer uploaded and website www.brightoakbuilders.com for inspiration.
List Our Services on Backside of business cards
Marcus Delling
Harborline Builders Inc.
Licensed General Contractors
858-471-6093

Contact Information for Business Card

Use the flyer uploaded and website www.brightoakbuilders.com for inspiration. List Our Services on Backside of business cards Marcus Delling Harborline Builders Inc. Licensed General Contractors 858-471-6093

```html
<!DOCTYPE html>
<html lang="en">
<head>
<meta charset="utf-8">
<title>Harborline Builders – Business Cards</title>
<link rel="stylesheet" href="https://fonts.googleapis.com/css2?family=Cinzel:wght@400&family=Oswald:wght@600&family=Roboto:wght@400;500&display=swap">
<style>
  :root {
    --bg: #6e6e6e;
    --bg-light: #8c8c8c;
    --ink: #151515;
    --paper: #ffffff;
    --accent-red: #e3121b;
    --accent-blue: #2f7fd1;
    --text-dark: #1b1b1b;
  }
  * { margin: 0; padding: 0; box-sizing: border-box; }
  html, body { width: 1200px; height: 1015px; overflow: hidden; }
  body {
    background: radial-gradient(ellipse at 50% 45%, var(--bg-light), var(--bg) 75%);
    font-family: "Roboto", Arial, sans-serif;
  }
  .card-stack {
    position: absolute; left: 250px; top: 70px;
    display: flex; flex-direction: column; gap: 75px;
  }
  .card {
    width: 700px; height: 400px; display: block;
    background: var(--paper);
    box-shadow: 0 12px 30px rgba(0,0,0,.35);
  }
  .band { fill: var(--ink); }
  .band-edge { stroke: var(--accent-blue); stroke-width: 4; fill: none; }
  .brand-name { font-family: "Cinzel", Georgia, serif; font-size: 25px; fill: var(--paper); letter-spacing: 1px; }
  .headline { font-family: "Oswald", "Arial Narrow", sans-serif; font-weight: 600; font-size: 21px; }
  .headline-red { fill: var(--accent-red); }
  .headline-white { fill: var(--paper); }
  .service { font-size: 16.5px; fill: var(--text-dark); }
  .bullet { fill: var(--accent-red); }
  .person-name { font-family: "Oswald", "Arial Narrow", sans-serif; font-weight: 600; font-size: 40px; fill: var(--accent-red); }
  .contact { font-size: 19px; fill: var(--text-dark); }
  .icon { fill: var(--accent-blue); }
  .icon-line { stroke: var(--accent-blue); fill: none; stroke-width: 1.6; }
  .company { font-size: 20px; font-weight: 500; fill: var(--accent-red); }
</style>
</head>
<body>
<main class="card-stack">

  <!-- Back side: services -->
  <svg class="card card-back" viewBox="0 0 700 400" xmlns="http://www.w3.org/2000/svg">
    <defs>
      <linearGradient id="photoWarm" x1="0" x2="1" y1="0" y2="0">
        <stop offset="0" stop-color="#fff" stop-opacity="0"/>
        <stop offset="0.35" stop-color="#e9d6bf"/>
        <stop offset="0.7" stop-color="#c99a6c"/>
        <stop offset="1" stop-color="#e4ddd3"/>
      </linearGradient>
    </defs>
    <polygon class="photo" role="img" aria-label="Photo of a bright renovated kitchen with wood floors"
             points="380,177 700,228 700,400 380,400" fill="url(#photoWarm)"/>
    <polygon class="band" points="0,0 700,0 700,228 0,108"/>
    <line class="band-edge" x1="0" y1="108" x2="700" y2="228"/>
    <text class="brand-name" x="670" y="165" text-anchor="end">HARBORLINE BUILDERS</text>
    <text class="headline headline-red" x="40" y="62">OUR SERVICES ARE 100% GUARENTEED</text>
    <text class="headline headline-white" x="40" y="92">SPECIALIZING IN</text>
    <g class="service-list">
      <circle class="bullet" cx="42" cy="158" r="4"/><text class="service" x="56" y="164">Remodel: Kitchen &amp; Bath</text>
      <circle class="bullet" cx="42" cy="180" r="4"/><text class="service" x="56" y="186">Painting: Interior &amp; Exterior</text>
      <circle class="bullet" cx="42" cy="202" r="4"/><text class="service" x="56" y="208">Flooring: Carpet, Vinyl, Wood</text>
      <circle class="bullet" cx="42" cy="224" r="4"/><text class="service" x="56" y="230">Window &amp; Door Replacement</text>
      <circle class="bullet" cx="42" cy="246" r="4"/><text class="service" x="56" y="252">Plumbing: Repairs &amp; Upgrades</text>
      <circle class="bullet" cx="42" cy="268" r="4"/><text class="service" x="56" y="274">Energy-Efficient Upgrades</text>
      <circle class="bullet" cx="42" cy="290" r="4"/><text class="service" x="56" y="296">Deck &amp; Patio Construction</text>
      <circle class="bullet" cx="42" cy="312" r="4"/><text class="service" x="56" y="318">Water &amp; Mold Damage</text>
      <circle class="bullet" cx="42" cy="334" r="4"/><text class="service" x="56" y="340">Garage Renovation</text>
    </g>
  </svg>

  <!-- Front side: contact -->
  <svg class="card card-front" viewBox="0 0 700 400" xmlns="http://www.w3.org/2000/svg">
    <defs>
      <linearGradient id="photoCool" x1="0" x2="1" y1="0" y2="0">
        <stop offset="0" stop-color="#fff" stop-opacity="0"/>
        <stop offset="0.4" stop-color="#e6e4e1"/>
        <stop offset="0.75" stop-color="#c9c4bd"/>
        <stop offset="1" stop-color="#b98f63"/>
      </linearGradient>
    </defs>
    <polygon class="photo" role="img" aria-label="Photo of a modern white living and dining room"
             points="330,169 700,228 700,400 330,400" fill="url(#photoCool)"/>
    <polygon class="band" points="0,0 700,0 700,228 0,108"/>
    <line class="band-edge" x1="0" y1="108" x2="700" y2="228"/>
    <text class="brand-name" x="670" y="165" text-anchor="end">HARBORLINE BUILDERS</text>

    <text class="person-name" x="58" y="198">MARCUS DELLING</text>

    <g class="contact-list">
      <path class="icon" d="M63 226c2-2 4-2 5 0l2 3c1 2 0 3-1 4 1 3 3 5 6 6 1-1 2-2 4-1l3 2c2 1 2 3 0 5-5 4-20-9-19-19z"/>
      <text class="contact" x="92" y="243">858-471-6093</text>
      <rect class="icon" x="62" y="258" width="20" height="14" rx="1"/>
      <path d="M62 259l10 8 10-8" stroke="#fff" stroke-width="1.6" fill="none"/>
      <text class="contact" x="92" y="272">info@brightoakbuilders.com</text>
      <circle class="icon-line" cx="72" cy="294" r="9"/>
      <ellipse class="icon-line" cx="72" cy="294" rx="4" ry="9"/>
      <line class="icon-line" x1="63" y1="294" x2="81" y2="294"/>
      <text class="contact" x="92" y="301">BrightOakBuilders.com</text>
    </g>

    <text class="company" x="58" y="345">Harborline Builders Inc.</text>
    <text class="company" x="58" y="371">Licensed General Contractors</text>
  </svg>

</main>
</body>
</html>
```